Organization and people consulting firm needs a website design

I need a website that promotes and explains the consulting service we will provide. The organization is called Bluefinch Advisory Partners. Our services include organization design, employee experience, change management, and executive coaching. I would like to see a simple clean and professional design, that reflects a modern and forward looking professional services company

Target Market(s)

Mid market and large companies

Industry/Entity Type

Management Consulting

Coding

Coded - Design and coding required

Number of Pages Required

5+ page

Font styles to use
Sans Serif

Colors

Designer to choose colors to be used in the design.

Requirements
Must have
• The following pages: Home, The Way We Work, What We Do, Our Founder, Insights, Contact.
• Search button.
• Hyper links (will be provided with main body text)
• Scrolling website with summaries at top level and links to more detail at lower level (like this website: veltracore.com)
• Company logo (uploaded)
• I have text for each of the pages that I can upload once the basic design is done
Should not have
• No clutter, keep the design clean

```html
<!DOCTYPE html>
<html lang="en">
<head>
<meta charset="utf-8">
<title>Bluefinch Advisory Partners</title>
<link href="https://fonts.googleapis.com/css2?family=Cinzel:wght@400;700&family=Crimson+Text:ital,wght@0,400;0,600;0,700;1,400&display=swap" rel="stylesheet">
<style>
:root{
  --red:#e0092c;
  --ink:#1c1c1c;
  --text:#555;
  --muted:#8a8a8a;
  --grey:#eef0f2;
  --line:#d9d9d9;
  --black:#050505;
  --white:#fff;
}
*{box-sizing:border-box;margin:0;padding:0}
html,body{width:1200px;height:4018px;overflow:hidden}
body{font-family:"Crimson Text",Georgia,serif;color:var(--text);background:var(--white);position:relative}
a{color:inherit;text-decoration:none}
.section{position:absolute;left:0;width:1200px}
.heading{font-family:"Cinzel",Georgia,serif;font-weight:700;color:var(--ink);text-align:center;font-size:36px;letter-spacing:1px;text-transform:uppercase}
.mark{display:block;width:22px;height:22px;border-radius:50%;background:var(--red);margin:0 auto}
.btn{display:inline-block;border:2px solid var(--red);border-radius:24px;color:var(--red);font-family:"Crimson Text",serif;font-weight:700;font-size:15px;text-transform:uppercase;letter-spacing:.5px;text-align:center;line-height:40px;height:44px}
.btn-solid{background:var(--red);color:var(--white)}

/* header */
.site-header{top:0;height:102px;background:var(--white);box-shadow:0 2px 6px rgba(0,0,0,.08);z-index:5}
.brand{position:absolute;left:100px;top:30px;display:flex;align-items:center;gap:10px}
.brand-dot{width:26px;height:26px;border-radius:50%;background:var(--red)}
.brand-name{font-family:"Crimson Text",serif;font-weight:700;font-size:30px;color:var(--red);line-height:1}
.main-nav{position:absolute;right:160px;top:38px;display:flex;gap:40px;font-size:17px;color:var(--ink)}
.main-nav .active{color:var(--red)}
.search-btn{position:absolute;right:99px;top:35px;width:36px;height:36px;border-radius:50%;background:var(--red)}
.search-btn svg{position:absolute;left:10px;top:10px}

/* hero */
.hero{top:102px;height:600px;background:linear-gradient(90deg,#ffffff 0%,#f4f4f4 35%,#e9e6e2 100%);overflow:hidden;border-bottom:8px solid var(--red)}
.hero-photo{position:absolute;right:0;top:0;width:720px;height:592px;background:linear-gradient(120deg,#f6f6f6 0%,#cfc8c0 40%,#4a4d55 70%,#2b2d33 100%)}
.hero-copy{position:absolute;left:102px;top:160px;width:620px}
.hero-title{font-family:"Cinzel",serif;font-weight:700;color:var(--red);font-size:58px;line-height:1}
.hero-sub{font-family:"Cinzel",serif;font-weight:700;color:var(--ink);font-size:40px;margin-top:10px}
.hero-text{font-size:18px;line-height:26px;color:#444;margin-top:12px;width:600px}
.hero .btn{margin-top:24px;width:150px;color:var(--ink);border-color:#444}
.hero-dots{position:absolute;left:550px;top:484px;display:flex;gap:8px}
.hero-dots span{width:12px;height:12px;border-radius:50%;border:2px solid var(--white)}
.hero-dots span.on{background:var(--white)}

/* way we work */
.way{top:724px;height:434px;text-align:center}
.way .mark{margin-top:26px}
.way .heading{margin-top:24px}
.way-text{width:810px;margin:22px auto 0;font-size:16px;line-height:32px}
.way .btn{margin-top:26px;width:155px}

/* what we do */
.services{top:1158px;height:624px;background:linear-gradient(180deg,#eef0f2,#e6e8eb)}
.services .mark{margin-top:80px}
.services .heading{margin-top:22px}
.service{position:absolute;width:330px}
.service.left{text-align:right}
.service h3{font-family:"Crimson Text",serif;font-weight:700;font-size:17px;color:var(--ink);text-transform:uppercase}
.service p{font-size:14px;line-height:20px;color:var(--muted);margin-top:4px}
.service a{display:block;color:var(--red);font-size:15px;font-weight:600;margin-top:4px}
.badge{position:absolute;width:130px;height:130px;border-radius:50%;background:#7c7c7c;box-shadow:0 4px 10px rgba(0,0,0,.2)}
.badge::after{content:"";position:absolute;left:16px;top:16px;width:98px;height:98px;border-radius:50%;background:var(--red);box-shadow:inset 0 0 0 6px rgba(255,255,255,.25)}
.service-divider{position:absolute;left:592px;top:412px;width:16px;height:16px;border-radius:50%;background:var(--red)}

/* founder */
.founder{top:1782px;height:796px;text-align:center}
.founder .mark{margin-top:76px}
.founder .heading{margin-top:24px}
.founder-text{width:820px;margin:20px auto 0;font-size:16px;line-height:30px}
.founder-photo{width:262px;height:262px;border-radius:50%;margin:26px auto 0;border:8px solid var(--white);box-shadow:0 2px 14px rgba(0,0,0,.25);background:radial-gradient(circle at 50% 40%,#d9c8b8 0%,#9a9089 45%,#6d7078 100%)}
.founder-name{font-size:28px;color:var(--ink);margin-top:18px}
.founder-role{font-size:16px;color:var(--text);margin-top:2px}
.founder .btn{margin-top:14px;width:232px}

/* insights */
.insights{top:2578px;height:678px;background:linear-gradient(180deg,#e9ebee,#dfe2e6 60%,#e8e9ec)}
.insights .mark{margin-top:80px}
.insights .heading{margin-top:22px}
.card{position:absolute;width:316px;background:var(--white);box-shadow:0 2px 10px rgba(0,0,0,.12);padding:28px 22px}
.card time{font-size:13px;color:var(--ink)}
.card h4{font-family:"Crimson Text",serif;font-weight:700;font-size:18px;color:var(--ink);margin-top:14px}
.card p{font-size:14px;line-height:21px;color:var(--muted);margin-top:8px}
.card a{display:block;color:var(--red);font-size:15px;font-weight:600;margin-top:8px}
.insights .btn{position:absolute;left:497px;top:576px;width:206px;background:var(--white)}

/* contact */
.contact{top:3256px;height:444px}
.contact-mark{position:absolute;left:322px;top:104px;width:36px;height:36px;border-radius:50%;background:var(--red)}
.contact-title{position:absolute;left:60px;top:166px;width:560px;font-family:"Cinzel",serif;font-weight:700;font-size:28px;line-height:46px;color:var(--ink);text-align:center;text-transform:uppercase}
.contact-address{position:absolute;left:250px;top:272px;font-size:17px;color:var(--text);display:flex;align-items:center;gap:8px}
.field{position:absolute;left:643px;width:443px;height:46px;border:1px solid var(--line);font-size:14px;color:#777;padding:12px 16px}
.field.msg{height:106px}
.contact .btn{position:absolute;left:951px;top:335px;width:135px}

/* footer */
.footer{top:3700px;height:318px;background:var(--black);border-top:8px solid var(--red)}
.social{position:absolute;top:112px;left:0;width:1200px;display:flex;justify-content:center;gap:14px}
.social span{width:50px;height:50px;border-radius:50%;border:2px solid var(--white)}
.footer-nav{position:absolute;top:188px;width:1200px;display:flex;justify-content:center;font-size:16px;color:var(--white)}
.footer-nav a{padding:0 26px;border-left:1px solid #888;line-height:18px}
.footer-nav a:first-child{border-left:none}
.copyright{position:absolute;top:228px;width:1200px;text-align:center;font-size:14px;color:var(--white)}
</style>
</head>
<body>

<header class="section site-header">
  <a class="brand" href="#"><span class="brand-dot"></span><span class="brand-name">Bluefinch</span></a>
  <nav class="main-nav">
    <a class="active" href="#">Home</a>
    <a href="#">The Way We Work</a>
    <a href="#">What We Do</a>
    <a href="#">Our Founder</a>
    <a href="#">Insights</a>
    <a href="#">Contact</a>
  </nav>
  <a class="search-btn" href="#" aria-label="Search"><svg width="16" height="16" viewBox="0 0 16 16"><circle cx="6.5" cy="6.5" r="4.5" fill="none" stroke="#fff" stroke-width="2"/><line x1="10" y1="10" x2="14" y2="14" stroke="#fff" stroke-width="2.4" stroke-linecap="round"/></svg></a>
</header>

<section class="section hero">
  <div class="hero-photo" role="img" aria-label="Photo of two consultants reviewing work on a tablet at a desk"></div>
  <div class="hero-copy">
    <h1 class="hero-title">Bluefinch</h1>
    <p class="hero-sub">Advisory Partners</p>
    <p class="hero-text">We are organisation &amp; people consulting firm, Our services include organisation design,employee experience, change management, &amp; executive coaching</p>
    <a class="btn" href="#">Read More</a>
  </div>
  <div class="hero-dots"><span class="on"></span><span></span><span></span><span></span><span></span></div>
</section>

<section class="section way">
  <span class="mark"></span>
  <h2 class="heading">The Way We Work</h2>
  <p class="way-text">Sed ut perspiciatis unde omnis iste natus error sit voluptatem accusantium doloremque laudantium, totam rem aperiam, eaque ipsa quae ab illo inventore veritatis et quasi architecto beatae vitae dicta sunt explicabo. Nemo enim ipsam voluptatem quia voluptas sit aspernatur aut odit aut fugit, sed quia cui dolorem ipsum quia doocmnqeuamtur magni dolores eos qui ratione voluptatem sequi nesciunt. Neque porro quisquam est, qui dolorem ipsum quia dolor sit amet, consectetur, adipisci velit, sed quia non numquam eius modi tempora incidunt ut labore et dolore magnam aliquam quaerat voluptatem.</p>
  <a class="btn" href="#">Read More</a>
</section>

<section class="section services">
  <span class="mark"></span>
  <h2 class="heading">What We Do</h2>

  <div class="service left" style="left:107px;top:238px">
    <h3>Organisation Design</h3>
    <p>At vero eos et accusamus et iusto odio dignissimos ducimus qui blanditiis praesentium voluptatum deleniti atque corrupti quos dolores et quas..</p>
    <a href="#">Read More &#187;</a>
  </div>
  <div class="badge" style="left:452px;top:238px"></div>
  <div class="badge" style="left:618px;top:238px"></div>
  <div class="service" style="left:763px;top:238px">
    <h3>Employee Experience</h3>
    <p>At vero eos et accusamus et iusto odio dignissimos ducimus qui blanditiis praesentium voluptatum deleniti atque corrupti quos dolores et quas..</p>
    <a href="#">Read More &#187;</a>
  </div>

  <span class="service-divider"></span>

  <div class="service left" style="left:107px;top:410px">
    <h3>Change Management</h3>
    <p>At vero eos et accusamus et iusto odio dignissimos ducimus qui blanditiis praesentium voluptatum deleniti atque corrupti quos dolores et quas..</p>
    <a href="#">Read More &#187;</a>
  </div>
  <div class="badge" style="left:452px;top:410px"></div>
  <div class="badge" style="left:618px;top:410px"></div>
  <div class="service" style="left:763px;top:410px">
    <h3>Executive Coaching</h3>
    <p>At vero eos et accusamus et iusto odio dignissimos ducimus qui blanditiis praesentium voluptatum deleniti atque corrupti quos dolores et quas..</p>
    <a href="#">Read More &#187;</a>
  </div>
</section>

<section class="section founder">
  <span class="mark"></span>
  <h2 class="heading">Our Founder</h2>
  <p class="founder-text">Sed ut perspiciatis unde omnis iste natus error sit voluptatem accusantium doloremque laudantium, totam rem aperiam, eaque ipsa quae ab illo inventore veritatis et quasi architecto beatae vitae dicta sunt explicabo. Nemo enim ipsam voluptatem quia voluptas sit aspernatur aut odit aut fugit, sed quia cui dolorem ipsum quia doocmnqeuamtur magni dolores.</p>
  <div class="founder-photo" role="img" aria-label="Portrait photo of the founder"></div>
  <p class="founder-name">Placeat Facere</p>
  <p class="founder-role">Founder</p>
  <a class="btn" href="#">More About Founder</a>
</section>

<section class="section insights">
  <span class="mark"></span>
  <h2 class="heading">Insights</h2>
  <article class="card" style="left:102px;top:225px;height:258px">
    <time>March 10,2018</time>
    <h4>Saepe eveniet ut et voluptates</h4>
    <p>Nam libero tempore, cum soluta nobis est eligendi optio cumque nihil impedit quo minus id quod maxime placeat facerededitis aut rerum necessitatibus..</p>
    <a href="#">Read More &#8594;</a>
  </article>
  <article class="card" style="left:442px;top:207px;height:296px">
    <time>March 10,2018</time>
    <h4>Et harum quidem rerum facest</h4>
    <p>Nam libero tempore, cum soluta nobis est eligendi optio cumque nihil impedit quo minus id quod maxime placeat facereTem- poribus autem quibusdam et aut officiisdebi- tis aut rerum necessitatibus..</p>
    <a href="#">Read More &#8594;</a>
  </article>
  <article class="card" style="left:783px;top:225px;height:258px">
    <time>March 10,2018</time>
    <h4>Temporibus autem quibust officiis</h4>
    <p>Nam libero tempore, cum soluta nobis est eligendi optio cumque nihil impedit quo minus id quod maxime placeat facerededitis aut rerum necessitatibus..</p>
    <a href="#">Read More &#8594;</a>
  </article>
  <a class="btn" href="#">View More Blogs</a>
</section>

<section class="section contact">
  <span class="contact-mark"></span>
  <h2 class="contact-title">Get In Touch With Us<br>And See How We Can Help</h2>
  <p class="contact-address"><svg width="12" height="16" viewBox="0 0 12 16"><path d="M6 0C2.7 0 0 2.6 0 5.9 0 10 6 16 6 16s6-6 6-10.1C12 2.6 9.3 0 6 0zm0 8.2A2.3 2.3 0 1 1 6 3.6a2.3 2.3 0 0 1 0 4.6z" fill="#444"/></svg>14 Larkspur Row, Suite 3</p>
  <div class="field" style="top:84px">Enter Name</div>
  <div class="field" style="top:139px">Enter Email</div>
  <div class="field msg" style="top:193px">Message</div>
  <a class="btn btn-solid" href="#">Get In Touch</a>
</section>

<footer class="section footer">
  <div class="social" aria-label="Social links"><span></span><span></span><span></span><span></span><span></span></div>
  <nav class="footer-nav">
    <a href="#">Home</a><a href="#">The Way We Work</a><a href="#">What We Do</a><a href="#">Our Founder</a><a href="#">Insights</a><a href="#">Contact</a>
  </nav>
  <p class="copyright">&copy; copyright 2018 Bluefinch Advisory Partners. All Rights Reserved</p>
</footer>

</body>
</html>
```